PillPeak website blog. Simple medical advice given in clear yes or no answers that save people money

I am developing a new web page that provides medical care cost savings at the consumers' fingertips. I need a web page that is clean, concise, and attractive for me to put my valuable medical information on. The information I provide is simple to obtain, yet very valuable to the consumer, and answered in a yes or no format. For example, A person may wonder if they need an antibiotic for cold like symptoms. Seeing a doctor for an antibiotic is very expensive. But with simple and clear advice at their fingertips, they can confidently avoid having to pay $200 or more to see a doctor and get an antibiotic. This is kind of like consumer reports for medical services.

Target Market(s)

People who are savvy shoppers and want to save money on healthcare. Likely younger ages between 21 and 60, who are mobile, readily use iphones, and want strong evidence based research to guide their decisions.

Industry/Entity Type

Coding

Number of Pages Required

Colors

Requirements
Must have
• A template on the "Question" and "Answer" page that can be edited many times that can be edited many times. The Confidence rating scale would need to be edited as well. The "Date Researched" the "PillPeak Pilluminate" and "References" all need to be able to be edited. This website must be very clear and simple to understand. A medical question is posed with a yes or no answer, then answered and given a confidence rating, we then tell them how much money they saved by going to our website.
Nice to have
• We want this to be slightly fun, vibrant, warm and inviting. This will be sometime later converted into an app format. Quirky, some humor to keep it interesting.
Should not have
• No sterile looking medical images. Not boring.

```html
<!DOCTYPE html>
<html lang="en">
<head>
<meta charset="utf-8">
<title>PillPeak — Clear. Valuable. Health.</title>
<link rel="stylesheet" href="https://fonts.googleapis.com/css2?family=Montserrat:wght@500;600;700&family=Jost:wght@500;600;700&display=swap">
<style>
:root{
  --blue:#1474c0;
  --hero:#4a86d8;
  --red:#e8232e;
  --ink:#1c1c1c;
  --grey:#9b9b9b;
  --line:#e4e4e4;
  --footer:#3b3b3b;
  --white:#ffffff;
}
*{box-sizing:border-box;margin:0;padding:0}
html,body{width:1200px;height:1033px;overflow:hidden;background:var(--white)}
body{position:relative;font-family:"Montserrat",sans-serif;color:var(--ink)}
.abs{position:absolute}

.brand{left:112px;top:52px;display:flex;align-items:center;gap:10px}
.brand-dot{width:22px;height:22px;border-radius:50%;background:var(--red)}
.brand-name{font-family:"Jost",sans-serif;font-weight:700;font-size:38px;color:var(--blue);line-height:1}

.search{left:386px;top:51px;width:305px;height:43px;border:1.5px solid #cfcfcf;border-radius:22px;display:flex;align-items:center}
.search span{padding-left:17px;font-size:13px;color:#666;flex:1}
.search button{width:110px;height:43px;margin-right:-1.5px;border:none;border-radius:22px;background:var(--blue);color:var(--white);font:600 14px "Montserrat",sans-serif}

.tagline-band{left:650px;top:0;width:550px;height:136px}
.tagline{left:735px;top:36px;width:372px;text-align:center;font-family:"Jost",sans-serif;font-weight:700;font-size:23px;letter-spacing:1.4px;line-height:31px;color:var(--white)}

.nav-rule{left:112px;top:159px;width:977px;height:2px;background:var(--line)}
.nav{left:111px;top:180px;width:979px;display:flex;justify-content:space-between;font-weight:600;font-size:15px;color:var(--ink)}

.hero{left:0;top:219px;width:1200px;height:560px;background:var(--hero)}
.side-menu{left:0;top:322px;display:flex;flex-direction:column;gap:6px}
.side-item{width:289px;height:54px;background:var(--white);border-radius:0 27px 27px 0;display:flex;align-items:center;font-weight:600;font-size:16.5px}
.side-icon{width:44px;height:48px;margin:0 16px 0 4px;display:flex;align-items:center;justify-content:center}
.side-icon.blue{background:var(--blue)}
.side-icon.red{background:var(--red)}

.hero-copy{left:320px;top:345px;width:330px;text-align:center;font-family:"Jost",sans-serif;font-weight:600;font-size:36px;line-height:50px;color:var(--white)}
.hero-btn{left:414px;top:568px;width:141px;height:45px;border:2.5px solid var(--white);border-radius:23px;display:flex;align-items:center;justify-content:center;font-family:"Jost",sans-serif;font-weight:600;font-size:17px;color:var(--white)}
.dots{left:455px;top:644px;display:flex;gap:5px}
.dots i{width:16px;height:16px;border-radius:50%;background:#a9c3ef}
.dots i:first-child{background:var(--white)}
.hero-art{left:695px;top:298px;width:340px;height:425px;border-radius:18px;background:linear-gradient(160deg,#3f63c9 0%,#5b8fe0 55%,#4a86d8 100%)}

.join-tab{left:378px;top:781px;width:444px;height:68px}
.join-title{left:378px;top:799px;width:444px;text-align:center;font-family:"Jost",sans-serif;font-weight:600;font-size:24px;color:var(--white)}
.email{left:291px;top:873px;width:494px;height:45px;border:1.5px solid #cfcfcf;border-radius:23px;padding-left:17px;display:flex;align-items:center;font-size:14px;color:#555}
.submit{left:793px;top:873px;width:118px;height:45px;border-radius:23px;background:var(--blue);color:var(--white);display:flex;align-items:center;justify-content:center;font-weight:600;font-size:15px}

.footer{left:0;top:958px;width:1200px;height:75px;background:var(--footer);color:var(--white);font-family:"Jost",sans-serif;font-weight:500}
.footer-left{position:absolute;left:112px;top:15px;font-size:16px;line-height:28px}
.footer-right{position:absolute;right:111px;top:13px;text-align:right;font-size:19px;line-height:28px}
.footer-right u{text-underline-offset:3px}
</style>
</head>
<body>

<div class="abs brand"><span class="brand-dot"></span><span class="brand-name">PillPeak</span></div>

<div class="abs search"><span>Search Here...</span><button>Search</button></div>

<svg class="abs tagline-band" viewBox="0 0 550 136" aria-hidden="true">
  <path d="M14 0 C60 20 72 50 72 80 C72 115 90 134 130 134 L550 134 L550 0 Z" fill="none" stroke="#e8232e" stroke-width="4"/>
  <path d="M10 0 C56 20 68 50 68 80 C68 114 86 131 126 131 L550 131 L550 0 Z" fill="#1474c0"/>
</svg>
<div class="abs tagline">CLEAR. VALUABLE. HEALTH.<br>ADVICE. RIGHT NOW.</div>

<div class="abs nav-rule"></div>
<nav class="abs nav">
  <span>Prev / Screening</span><span>Women's Health</span><span>Men's Health</span><span>Meds</span><span>Surgery</span><span>Imaging</span><span>Peds</span><span>Contact Us</span>
</nav>

<section class="abs hero"></section>

<div class="abs side-menu">
  <div class="side-item"><span class="side-icon blue"><svg width="22" height="22" viewBox="0 0 22 22"><circle cx="11" cy="11" r="9" fill="none" stroke="#fff" stroke-width="2"/><path d="M8 8.5a3 3 0 1 1 4 2.8c-.8.4-1 .9-1 1.7" fill="none" stroke="#fff" stroke-width="2"/><circle cx="11" cy="16" r="1.2" fill="#fff"/></svg></span>Who Are We?</div>
  <div class="side-item"><span class="side-icon red"><svg width="24" height="22" viewBox="0 0 24 22"><path d="M3 8l9-5 9 5-9 5zM3 12l9 5 9-5M3 16l9 5 9-5" fill="none" stroke="#fff" stroke-width="1.8"/></svg></span>How It Works?</div>
  <div class="side-item"><span class="side-icon blue"><svg width="26" height="22" viewBox="0 0 26 22"><path d="M2 4h9c1 0 2 1 2 2v14c0-1-1-2-2-2H2zM24 4h-9c-1 0-2 1-2 2v14c0-1 1-2 2-2h9z" fill="none" stroke="#fff" stroke-width="1.6"/></svg></span>Evidence Based Research</div>
  <div class="side-item"><span class="side-icon red"><svg width="22" height="24" viewBox="0 0 22 24"><circle cx="11" cy="7" r="5" fill="none" stroke="#fff" stroke-width="1.8"/><path d="M2 23c0-6 4-9 9-9s9 3 9 9" fill="none" stroke="#fff" stroke-width="1.8"/></svg></span>Dr. Whitmore</div>
  <div class="side-item"><span class="side-icon blue"><svg width="22" height="24" viewBox="0 0 22 24"><circle cx="11" cy="7" r="5" fill="none" stroke="#fff" stroke-width="1.8"/><path d="M2 23c0-6 4-9 9-9s9 3 9 9z" fill="#fff"/></svg></span>Who We Are Not</div>
  <div class="side-item"><span class="side-icon red"><svg width="26" height="22" viewBox="0 0 26 22"><path d="M13 2v18M5 20h16M4 5h18M4 5l-3 8h6zM22 5l-3 8h6z" fill="none" stroke="#fff" stroke-width="1.6"/></svg></span>Are We Biased?</div>
</div>

<h1 class="abs hero-copy">Save $1,000 per Year On Healthcare. It’s Free!</h1>
<div class="abs hero-btn">Click Here!</div>
<div class="abs dots"><i></i><i></i><i></i></div>
<div class="abs hero-art" role="img" aria-label="Illustration of a woman holding a phone consulting a doctor on a large smartphone screen, with a plant, pill packs and a stethoscope"></div>

<svg class="abs join-tab" viewBox="0 0 444 68" aria-hidden="true">
  <path d="M0 0 H444 C420 8 412 20 410 36 C408 58 398 68 372 68 H72 C46 68 36 58 34 36 C32 20 24 8 0 0 Z" fill="#9b9b9b"/>
</svg>
<h2 class="abs join-title">Become A PillPeak Today!</h2>
<div class="abs email">Enter Email</div>
<div class="abs submit">Submit</div>

<footer class="abs footer">
  <div class="footer-left">Copyrights @ 2018 PillPeak. All Rights Reserved.<br>Disclaimer: Nemo enim ipsam voluptatem quia voluptas quae ab illo inventore</div>
  <div class="footer-right">Ask a question here!<br><u>If it is worthy, Well post it!</u></div>
</footer>

</body>
</html>
```